Computer consultant business card

Bexil Software is a newly started computer consulting company. It's a small one-man company that provides mostly Vornix applications but also websites in collaboration with designers. I'm running this company on the side of full time university studies.

I want the final design to be clean and memorable. Be creative! :)

Some inspiration:
http://www.pixelmarta.com/design/48317
http://www.pixelmarta.com/design/2739164/business-card-design-by-frostlynk
http://www.pixelmarta.com/design/604281/business-card-design-by-koralind-vestrabanu

See attachment for my company logo.
Updates

I would like to thank everyone for submitting! I'll need a couple of days to review and ultimately select a design.

Target Market(s)

Non-technical entrepreneurs and small companies.

Industry/Entity Type

University

Requirements
Must have
• My company logo.
In any way, both colors from my logo.
First- and last name, e-mail and phone number.
Double-sided design.
Nice to have
• Something creative with the symbol in my logo

```html
<!DOCTYPE html>
<html lang="en">
<head>
<meta charset="utf-8">
<title>Zorvi – Business Card Concepts</title>
<link rel="stylesheet" href="https://fonts.googleapis.com/css2?family=Jost:wght@400;500;600&display=swap">
<style>
  :root {
    --stage: #e8e4de;
    --label: #1c1c1c;
    --card-charcoal: #333132;
    --card-black: #050505;
    --card-white: #ffffff;
    --brand-blue: #4a72bb;
    --ink-light: #ffffff;
    --ink-dark: #333132;
    --pattern-tone: #5a5558;
  }
  * { box-sizing: border-box; margin: 0; padding: 0; }
  html, body { width: 788px; height: 1200px; overflow: hidden; }
  body {
    position: relative;
    background: var(--stage);
    font-family: "Jost", sans-serif;
  }
  .concept-label {
    position: absolute;
    width: 300px;
    text-align: center;
    font-size: 21px;
    font-weight: 400;
    color: var(--label);
  }
  .card {
    position: absolute;
    width: 300px;
    height: 525px;
    border-radius: 18px;
    overflow: hidden;
    box-shadow: 0 2px 6px rgba(0,0,0,0.25);
  }
  .card--front { left: 72px; top: 55px; background: var(--card-charcoal); }
  .card--back-symbol { left: 444px; top: 55px; background: var(--card-charcoal); }
  .card--back-dark { left: 72px; top: 655px; background: var(--card-black); }
  .card--back-light { left: 444px; top: 655px; background: var(--card-white); }

  .brand {
    position: absolute;
    left: 0; right: 0;
    display: flex;
    justify-content: center;
    align-items: center;
    gap: 12px;
  }
  .brand__mark {
    width: 46px; height: 46px;
    border-radius: 50%;
    background: var(--brand-blue);
  }
  .brand__name {
    font-size: 52px;
    font-weight: 500;
    line-height: 1;
    letter-spacing: 1px;
    color: var(--ink-light);
  }
  .brand--on-light .brand__name { color: var(--ink-dark); }

  .card--front .brand { top: 92px; }
  .holder {
    position: absolute;
    top: 293px; left: 0; right: 0;
    text-align: center;
    color: var(--ink-light);
  }
  .holder__name { font-size: 17px; font-weight: 600; letter-spacing: 0.3px; }
  .holder__role { font-size: 12px; font-weight: 400; margin-top: 2px; }
  .contact {
    position: absolute;
    top: 450px; left: 0; right: 0;
    list-style: none;
    text-align: center;
    color: var(--ink-light);
    font-size: 13px;
    line-height: 18px;
  }
  .contact svg { width: 9px; height: 9px; margin-right: 3px; vertical-align: 0; fill: var(--ink-light); }

  .hero-brand {
    position: absolute;
    top: 215px; left: 0; right: 0;
    display: flex;
    justify-content: center;
    align-items: center;
    gap: 14px;
  }
  .hero-brand__mark {
    width: 64px; height: 64px;
    border-radius: 50%;
    background: var(--brand-blue);
  }
  .hero-brand__name {
    font-size: 76px;
    font-weight: 500;
    line-height: 1;
    color: var(--ink-light);
  }

  .texture {
    position: absolute;
    width: 230px; height: 230px;
  }
  .texture--top {
    right: -40px; top: 30px;
    background: radial-gradient(ellipse at center, var(--pattern-tone) 0%, rgba(90,85,88,0.35) 40%, rgba(5,5,5,0) 70%);
  }
  .texture--bottom {
    left: -40px; bottom: 20px;
    background: radial-gradient(ellipse at center, var(--pattern-tone) 0%, rgba(90,85,88,0.35) 40%, rgba(5,5,5,0) 70%);
  }
  .card--back-dark .brand { top: 232px; }
  .card--back-light .brand { top: 232px; }
</style>
</head>
<body>

  <p class="concept-label" style="left:72px; top:20px;">Front</p>
  <p class="concept-label" style="left:444px; top:20px;">Back - 1</p>
  <p class="concept-label" style="left:72px; top:608px;">Back - 2</p>
  <p class="concept-label" style="left:444px; top:608px;">Back - 3</p>

  <section class="card card--front">
    <div class="brand">
      <span class="brand__mark"></span>
      <span class="brand__name">zorvi</span>
    </div>
    <div class="holder">
      <p class="holder__name">First Name + Last Name</p>
      <p class="holder__role">Designation</p>
    </div>
    <ul class="contact">
      <li><svg viewBox="0 0 10 10" aria-hidden="true"><path d="M2 0.5 L3.8 2.6 L2.8 3.8 Q4 6 6.2 7.2 L7.4 6.2 L9.5 8 L8.3 9.5 Q3.5 8.8 0.5 1.7 Z"/></svg>+12 345 6789</li>
      <li><svg viewBox="0 0 10 10" aria-hidden="true"><path d="M0.5 2 H9.5 V8.5 H0.5 Z M0.5 2 L5 5.5 L9.5 2" /></svg>info@website.com</li>
    </ul>
  </section>

  <section class="card card--back-symbol">
    <div class="hero-brand">
      <span class="hero-brand__mark"></span>
      <span class="hero-brand__name">zorvi</span>
    </div>
  </section>

  <section class="card card--back-dark">
    <div class="texture texture--top" role="img" aria-label="Decorative dot texture fading in from the upper right"></div>
    <div class="texture texture--bottom" role="img" aria-label="Decorative dot texture fading in from the lower left"></div>
    <div class="brand">
      <span class="brand__mark"></span>
      <span class="brand__name">zorvi</span>
    </div>
  </section>

  <section class="card card--back-light">
    <div class="brand brand--on-light">
      <span class="brand__mark"></span>
      <span class="brand__name">zorvi</span>
    </div>
  </section>

</body>
</html>
```